KRT Engineering Business Card Design

We’re looking for an elegant, clean, and timeless business card design that communicates experience, capability, and reliability.

KRT Engineering was established in 1995 , we are a Government Contracting company providing Professional Services to the Office of Frontier Affairs, Harbor Protection and the Vantage Collective. Our capabilities include: Acquisition & Program Management; Intelligence & Security Operations; Cyber, IT & Network Operations; Lifecycle Logistics & Asset Readiness; C5ISR Systems Engineering & Sustainment.

We want the card to reflect a straightforward, confident approach to business. The design should feel polished and professional without being flashy or overly corporate.

Design Direction
Clean, sophisticated, and uncluttered
Elegant but understated
Strong typography and thoughtful spacing
A timeless aesthetic rather than something overly trendy
Confident and established, with a sense of substance
Easy to read and practical in a real-world business setting

The overall impression should be: “These are experienced professionals who know what they’re doing, do what they say, and can be relied upon.”

We’re open to creative interpretations. The finished card should feel distinctive through its typography, proportions, layout, and attention to detail rather than through excessive graphics or visual effects.

We’re looking for a design that would make a potential client immediately feel that they’re dealing with a capable, trustworthy, and established company.

Company Colors: Navy and Gold/Yellow (but you do not need to use these colors on the card)
Company Name: KRT Engineering Associates, Inc. (known as KRT Engineering)
Website: krtengineering.com
Company Logo: Navy & Gold (other variations attached)

```html
<!DOCTYPE html>
<html lang="en">
<head>
<meta charset="utf-8">
<title>KRT Engineering — Business Card</title>
<link href="https://fonts.googleapis.com/css2?family=Poppins:wght@300;400;600;800&display=swap" rel="stylesheet">
<style>
  :root {
    --navy: #222c5f;
    --gold: #fde24a;
    --white: #ffffff;
    --ink-grey: #55575e;
    --stage: #e6e7ea;
  }
  * { box-sizing: border-box; margin: 0; padding: 0; }
  html, body { width: 1200px; height: 985px; overflow: hidden; }
  body {
    background: var(--stage);
    font-family: "Poppins", sans-serif;
    display: flex;
    flex-direction: column;
    align-items: center;
    justify-content: center;
    gap: 48px;
  }
  .card {
    position: relative;
    width: 720px;
    height: 412px;
    border-radius: 26px;
    overflow: hidden;
    box-shadow: 0 10px 28px rgba(20, 24, 50, 0.18);
  }
  .card-shapes { position: absolute; inset: 0; width: 100%; height: 100%; }

  /* Front */
  .front { background: var(--navy); }
  .front .wordmark {
    position: absolute;
    left: 56px;
    top: 92px;
    font-weight: 800;
    font-size: 104px;
    line-height: 1;
    letter-spacing: -2px;
    color: var(--navy);
  }
  .front .divider {
    position: absolute;
    left: 292px;
    top: 100px;
    width: 1.5px;
    height: 150px;
    background: var(--navy);
    opacity: 0.7;
  }
  .contact {
    position: absolute;
    left: 318px;
    top: 100px;
    color: var(--navy);
  }
  .contact .person-name {
    font-weight: 800;
    font-size: 21px;
    letter-spacing: 0.5px;
    line-height: 1.1;
  }
  .contact .person-role {
    font-weight: 400;
    font-size: 15px;
    color: var(--ink-grey);
    margin-bottom: 14px;
  }
  .contact-list { list-style: none; }
  .contact-list li {
    display: flex;
    align-items: center;
    gap: 10px;
    font-size: 14.5px;
    color: var(--ink-grey);
    margin-bottom: 7px;
  }
  .contact-icon {
    width: 20px; height: 20px;
    border-radius: 50%;
    background: var(--gold);
    display: flex; align-items: center; justify-content: center;
    flex-shrink: 0;
  }
  .contact-icon svg { width: 11px; height: 11px; }
  .address {
    position: absolute;
    left: 40px;
    bottom: 38px;
    font-size: 14px;
    color: var(--ink-grey);
  }

  /* Back */
  .back {
    background: var(--navy);
    display: flex;
    flex-direction: column;
    align-items: center;
    justify-content: center;
    gap: 18px;
  }
  .back .wordmark {
    font-weight: 800;
    font-size: 128px;
    line-height: 1;
    letter-spacing: -2px;
    color: var(--white);
  }
  .back .website {
    font-weight: 300;
    font-size: 16px;
    letter-spacing: 4px;
    color: var(--white);
  }
</style>
</head>
<body>

  <section class="card front" aria-label="Business card front">
    <svg class="card-shapes" viewBox="0 0 720 412" preserveAspectRatio="none" aria-hidden="true">
      <path class="band-gold" fill="var(--gold)"
            d="M70,0 L670,0 C724,140 722,300 676,412 L0,412 L0,0 Z"/>
      <path class="panel-white" fill="var(--white)"
            d="M0,0 L120,0 C380,18 600,110 636,240 C656,320 612,386 520,412 L0,412 Z"/>
    </svg>

    <div class="wordmark">KRT</div>
    <div class="divider"></div>

    <div class="contact">
      <p class="person-name">ALAN REEVES</p>
      <p class="person-role">Manager</p>
      <ul class="contact-list">
        <li>
          <span class="contact-icon">
            <svg viewBox="0 0 24 24"><path fill="var(--navy)" d="M6.6 10.8a15.1 15.1 0 0 0 6.6 6.6l2.2-2.2c.3-.3.7-.4 1-.2 1.1.4 2.3.6 3.6.6.6 0 1 .4 1 1V20c0 .6-.4 1-1 1A17 17 0 0 1 3 4c0-.6.4-1 1-1h3.5c.6 0 1 .4 1 1 0 1.3.2 2.5.6 3.6.1.3 0 .7-.2 1z"/></svg>
          </span>
          757-310-2846
        </li>
        <li>
          <span class="contact-icon">
            <svg viewBox="0 0 24 24"><path fill="var(--navy)" d="M2 5h20v14H2z"/><path fill="none" stroke="var(--gold)" stroke-width="2" d="M2 6l10 7 10-7"/></svg>
          </span>
          alan.reeves@krtmail.com
        </li>
        <li>
          <span class="contact-icon">
            <svg viewBox="0 0 24 24"><circle cx="12" cy="12" r="10" fill="none" stroke="var(--navy)" stroke-width="2.4"/><path fill="none" stroke="var(--navy)" stroke-width="2" d="M2 12h20M12 2c3 3 3 17 0 20M12 2c-3 3-3 17 0 20"/></svg>
          </span>
          www.krtengineering.com
        </li>
      </ul>
    </div>

    <p class="address">1420 Harbor View Road, Suite 310, Norfolk, VA 23510</p>
  </section>

  <section class="card back" aria-label="Business card back">
    <div class="wordmark">KRT</div>
    <p class="website">www.krtengineering.com</p>
  </section>

</body>
</html>
```